Business card for Luxury Portable Restroom Trailer company

We are a Luxury Portable Restroom Trailer Company Called FALCRIDGE HIRES. Based in Orange County California. We provide portable restroom trailers for events, such as, Weddings, Concerts, Charity events, Sporting events, Tournaments, Corporate events, ect. We rent and Sell the Luxury restrooms. Our colors are white, grey, and Orange. As you will see in the logo we uploaded.
There are 2 people in the company so the names and titles will change for the 3 people but card will remain the same. Here is the information for each Person: Dwight Penner CFO 555 318-0476
next Person: Leon Marchetti VP 555 318-0476
Next Person: Owen Marchetti CEO 555 318-0476
Information to include on the card: Luxury Restroom Trailers Rental and Sales. Weddings, Concerts, Charity, Sporting and Corp. Events.

```html
<!DOCTYPE html>
<html lang="en">
<head>
<meta charset="utf-8">
<title>Falcridge Hires – Business Card</title>
<link rel="stylesheet" href="https://fonts.googleapis.com/css2?family=Montserrat:wght@400;500;600;800&display=swap">
<style>
  :root {
    --orange: #e65c20;
    --orange-light: #ee7435;
    --orange-deep: #dc5219;
    --grey: #4a4a4c;
    --white: #ffffff;
    --backdrop: #c8c8c8;
  }
  * { box-sizing: border-box; margin: 0; padding: 0; }
  html, body {
    width: 1200px; height: 802px; overflow: hidden;
    background: var(--backdrop);
    font-family: "Montserrat", sans-serif;
  }
  .canvas { position: relative; width: 1200px; height: 802px; }
  .card {
    position: absolute; top: 246px;
    width: 540px; height: 310px;
    border-radius: 22px; overflow: hidden;
    box-shadow: 0 10px 24px rgba(0,0,0,0.22);
  }
  /* Front side */
  .card-front { left: 40px; background: var(--white); }
  .front-brand {
    position: absolute; left: 36px; top: 40px;
    font-weight: 800; font-size: 28px; line-height: 1;
    letter-spacing: 1px; color: var(--orange);
  }
  .front-ring {
    position: absolute; right: 36px; top: 32px;
    width: 112px; height: 112px;
  }
  .person-accent {
    position: absolute; left: 0; top: 142px;
    width: 14px; height: 34px; background: var(--orange);
  }
  .person-name {
    position: absolute; left: 36px; top: 138px;
    font-weight: 800; font-size: 24px; letter-spacing: 1.5px;
    color: var(--orange); text-transform: uppercase;
  }
  .person-title {
    position: absolute; left: 38px; top: 170px;
    font-weight: 500; font-size: 15px; color: var(--grey);
  }
  .contact-list {
    position: absolute; left: 38px; top: 208px;
    list-style: none;
  }
  .contact-list li {
    display: flex; align-items: center; gap: 9px;
    font-size: 15px; font-weight: 400; color: var(--grey);
    height: 24px; letter-spacing: 0.3px;
  }
  .contact-icon { width: 13px; height: 13px; flex: none; }
  /* Back side */
  .card-back {
    left: 620px;
    background: linear-gradient(150deg, var(--orange-light) 0%, var(--orange) 45%, var(--orange-deep) 100%);
  }
  .back-decoration {
    position: absolute; left: 120px; top: -20px;
    width: 360px; height: 350px; border-radius: 50%;
    background: radial-gradient(circle at 50% 45%, rgba(255,255,255,0.10), rgba(255,255,255,0) 70%);
  }
  .back-content {
    position: absolute; inset: 0;
    display: flex; flex-direction: column;
    align-items: center; justify-content: center;
    text-align: center; color: var(--white);
  }
  .back-brand {
    font-weight: 800; font-size: 40px; letter-spacing: 2px; line-height: 1.1;
  }
  .back-rule {
    width: 300px; height: 2px; background: var(--white);
    margin: 16px 0 14px;
  }
  .back-service {
    font-weight: 600; font-size: 15px; letter-spacing: 1px;
    text-transform: uppercase;
  }
  .back-events {
    margin-top: 8px;
    font-weight: 400; font-size: 13px; letter-spacing: 0.3px;
  }
</style>
</head>
<body>
<main class="canvas">
  <section class="card card-front" aria-label="Business card front">
    <div class="front-brand">FALCRIDGE HIRES</div>
    <svg class="front-ring" viewBox="0 0 112 112" aria-hidden="true">
      <circle cx="56" cy="56" r="51" fill="none" stroke="var(--orange)" stroke-width="6"/>
    </svg>
    <span class="person-accent"></span>
    <h1 class="person-name">Owen Marchetti</h1>
    <p class="person-title">CEO</p>
    <ul class="contact-list">
      <li>
        <svg class="contact-icon" viewBox="0 0 16 16" aria-hidden="true"><path fill="var(--orange)" d="M3.6 1.2l2.3 2.6-1.3 2a8 8 0 0 0 5.6 5.6l2-1.3 2.6 2.3-1.4 2.3C7 14.8 1.2 9 1.3 2.6z"/></svg>
        555 318-0476
      </li>
      <li>
        <svg class="contact-icon" viewBox="0 0 16 16" aria-hidden="true"><rect x="1" y="3" width="14" height="10" rx="1.5" fill="var(--orange)"/><path d="M2 4.5l6 4.5 6-4.5" fill="none" stroke="#fff" stroke-width="1.4"/></svg>
        owen@falcridgehires.com
      </li>
      <li>
        <svg class="contact-icon" viewBox="0 0 16 16" aria-hidden="true"><circle cx="8" cy="8" r="7" fill="var(--orange)"/><path d="M1 8h14M8 1c-3 3.5-3 10.5 0 14M8 1c3 3.5 3 10.5 0 14" fill="none" stroke="#fff" stroke-width="1"/></svg>
        www.falcridgehires.com
      </li>
    </ul>
  </section>

  <section class="card card-back" aria-label="Business card back">
    <div class="back-decoration" role="img" aria-label="Large faint brand emblem watermark"></div>
    <div class="back-content">
      <div class="back-brand">FALCRIDGE HIRES</div>
      <span class="back-rule"></span>
      <p class="back-service">Luxury Restroom Trailers Rental and Sales</p>
      <p class="back-events">Weddings, Concerts, Charity, Sporting and Corp. Events.</p>
    </div>
  </section>
</main>
</body>
</html>
```